Building company buisness cards

We are looking for a sharp modern new look for our business cards.We are a New Zealand based company that specialises in house and land packages.We have attached a photo of the current logo and would like to see if it can be improved somehow if needed.We are open to any colours but we have chosen Black and White at this stage. Feel free to change the font and make the logo smarter looking.Play with the colours and see what looks best.We want a card that looks so good know one will want to throw it away!

Target Market(s)

Building profesonals, home buyers

Industry/Entity Type

Building

Contact Information for Business Card

Garrick Tenwood
0275390628
garrickt@hartvale.co.nz

Font styles to use
Serif
Sans Serif

Colors

Designer to choose colors to be used in the design.

Requirements
Must have
• Just the logo on one side and details on the other
• Clean simple looking card
Nice to have
• Round corners and detail like raised or spot UV
• Something that stands out
Should not have
• To title needed, Director etc

```html
<!DOCTYPE html>
<html lang="en">
<head>
<meta charset="utf-8">
<title>Hartvale business card</title>
<link rel="stylesheet" href="https://fonts.googleapis.com/css2?family=Playfair+Display:wght@700&family=Roboto:wght@400&display=swap">
<style>
  :root {
    --navy: #1e2858;
    --orange: #ec9a27;
    --white: #ffffff;
    --ink: #4a4a4a;
    --backdrop: #e4e4e4;
  }
  * { margin: 0; padding: 0; box-sizing: border-box; }
  html, body { width: 1125px; height: 1200px; overflow: hidden; }
  body { background: var(--backdrop); position: relative; font-family: "Roboto", sans-serif; }

  .card {
    position: absolute;
    left: 171px;
    width: 824px;
    height: 470px;
    border-radius: 24px;
    overflow: hidden;
  }
  .card--front { top: 106px; background: var(--white); }
  .card--back { top: 638px; background: var(--navy); }

  .name-band {
    position: absolute;
    left: 0; top: 93px;
    width: 396px; height: 74px;
    background: var(--navy);
    display: flex; align-items: center;
    padding-left: 45px;
  }
  .holder-name {
    font-family: "Playfair Display", serif;
    font-weight: 700;
    font-size: 25px;
    letter-spacing: 0.5px;
    color: var(--white);
    text-transform: uppercase;
    white-space: nowrap;
  }
  .accent-band {
    position: absolute;
    left: 715px; top: 79px;
    width: 109px; height: 100px;
    background: var(--orange);
  }
  .wordmark {
    font-family: "Playfair Display", serif;
    font-weight: 700;
    line-height: 1;
    white-space: nowrap;
  }
  .wordmark--front {
    position: absolute;
    left: 404px; top: 88px;
    font-size: 66px;
    color: var(--navy);
  }

  .contact-list {
    position: absolute;
    left: 44px; top: 315px;
    list-style: none;
  }
  .contact-list li {
    display: flex; align-items: center;
    height: 27px;
    font-size: 19px;
    color: var(--ink);
  }
  .contact-list svg { width: 20px; height: 20px; margin-right: 12px; flex: none; }

  .back-logo {
    position: absolute;
    left: 0; right: 0; top: 160px;
    text-align: center;
  }
  .wordmark--back { font-size: 96px; color: var(--white); }
  .back-url {
    position: absolute;
    left: 0; right: 0; top: 386px;
    text-align: center;
    font-size: 19px;
    letter-spacing: 7px;
    color: var(--white);
  }
</style>
</head>
<body>
  <section class="card card--front">
    <div class="name-band"><span class="holder-name">Garrick Tenwood</span></div>
    <div class="accent-band"></div>
    <span class="wordmark wordmark--front">Hartvale</span>
    <ul class="contact-list">
      <li>
        <svg viewBox="0 0 24 24" aria-hidden="true"><path fill="var(--navy)" d="M6.6 10.8a15.1 15.1 0 0 0 6.6 6.6l2.2-2.2c.3-.3.7-.4 1-.2 1.1.4 2.3.6 3.6.6.6 0 1 .4 1 1V20c0 .6-.4 1-1 1A17 17 0 0 1 3 4c0-.6.4-1 1-1h3.5c.6 0 1 .4 1 1 0 1.3.2 2.5.6 3.6.1.3 0 .7-.2 1z"/></svg>
        0275390628
      </li>
      <li>
        <svg viewBox="0 0 24 24" aria-hidden="true"><rect x="3" y="6" width="18" height="12" fill="none" stroke="var(--navy)" stroke-width="2"/><path d="M3 6l9 7 9-7" fill="none" stroke="var(--navy)" stroke-width="2"/></svg>
        garrickt@hartvale.co.nz
      </li>
      <li>
        <svg viewBox="0 0 24 24" aria-hidden="true"><circle cx="12" cy="12" r="9" fill="var(--navy)"/><path d="M8 7c2 1 1 3 3 3s1 3 3 3M14 6c-1 2 2 3 3 2M9 15c1 0 2 2 1 4" fill="none" stroke="var(--white)" stroke-width="1.6"/></svg>
        www.hartvale.co.nz
      </li>
    </ul>
  </section>

  <section class="card card--back">
    <div class="back-logo">
      <span class="wordmark wordmark--back">Hartvale</span>
    </div>
    <p class="back-url">www.Hartvale.co.nz</p>
  </section>
</body>
</html>
```